Caldrift - Where every box finds its place!

Hello,
I'd like to update, re-vamp, and re-tool this current power point presentation with slightly more professional appearance as well as more accurately reflect the website -caldrift.com- color scheme and sleek design scheme. Please see attached.
We at Caldrift pride ourselves on seeking to rework an archaic business into something progressive, cost effective, more reliable, and easily accessible in todays fast growing market that has only gotten more expensive, more costly and less indirect over the last couple years.

Target Market(s)

New updated and hassle free moving opportunities no matter how large or how small in a market that begs for a change

Industry/Entity Type

Logistics/Moving

Requirements
Must have
• The current color scheme from the -caldrift.com- website as well as the inclusion of the current data on the sample power point presentation provided but with updated graphics

```html
<!DOCTYPE html>
<html lang="en">
<head>
<meta charset="utf-8">
<title>Caldrift – Company Presentation</title>
<link href="https://fonts.googleapis.com/css2?family=Lato:wght@400;700;900&display=swap" rel="stylesheet">
<style>
  :root{
    --blue:#1652c8;
    --blue-deep:#0d3a99;
    --yellow:#f7c21b;
    --gold:#bf9516;
    --ink:#111827;
    --text:#5b6270;
    --page:#eef0f4;
    --white:#ffffff;
  }
  *{box-sizing:border-box;margin:0;padding:0}
  html,body{width:1200px;height:4172px;overflow:hidden}
  body{background:var(--page);font-family:'Lato',sans-serif;color:var(--ink);position:relative}
  .slide{position:absolute;left:100px;width:1000px;height:562px;background:var(--white);overflow:hidden;box-shadow:0 6px 24px rgba(20,40,90,.12)}
  .slide-welcome{top:20px}
  .slide-about{top:700px}
  .slide-vision{top:1380px}
  .slide-checks{top:2060px}
  .slide-label{top:2740px}
  .slide-thanks{top:3420px}
  .side-bars{position:absolute;inset:0;width:1000px;height:562px}
  .photo{position:absolute}
  .brand{display:flex;align-items:center;gap:12px;font-weight:900;font-size:30px}
  .brand-mark{width:22px;height:22px;border-radius:50%}
  .heading{font-weight:900;text-transform:uppercase;letter-spacing:.5px}
  .body-copy{font-size:12.5px;line-height:1.65;color:var(--text)}

  /* Welcome */
  .slide-welcome{background:var(--blue)}
  .welcome-bg{position:absolute;inset:0;background:linear-gradient(100deg,#1652c8 0%,#1a5fd8 45%,#2f72e0 75%,#1a55c4 100%)}
  .slide-welcome .brand{position:absolute;left:50px;top:54px;color:var(--white)}
  .slide-welcome .brand-mark{background:var(--yellow)}
  .welcome-title{position:absolute;left:50px;top:220px;color:var(--white);font-size:54px;line-height:1.08}
  .welcome-tagline{position:absolute;left:52px;top:352px;color:var(--yellow);font-size:24px;font-weight:700}

  /* About */
  .about-frame{position:absolute;left:90px;top:96px;width:250px;height:380px;background:var(--yellow)}
  .about-photo{left:108px;top:114px;width:214px;height:344px;background:linear-gradient(160deg,#c9d3de,#8e9aa8 55%,#5d6775)}
  .about-text{position:absolute;left:410px;top:130px;width:500px}
  .about-text .heading{font-size:32px;margin-bottom:18px}
  .about-text .body-copy+.body-copy{margin-top:12px}

  /* Vision */
  .centered-title{position:absolute;left:0;right:0;text-align:center}
  .slide-vision .heading,.slide-checks .heading{font-size:30px}
  .vision-sub{top:100px;font-size:14px;color:var(--text)}
  .vision-card{position:absolute;top:168px;width:180px;height:340px;border-radius:90px;text-align:center;color:var(--white);padding:196px 20px 0}
  .vision-card.blue{background:var(--blue)}
  .vision-card.yellow{background:var(--yellow);color:var(--ink)}
  .vision-card .card-photo{position:absolute;left:12px;top:12px;width:156px;height:156px;border-radius:50%;border:5px solid var(--white)}
  .vision-card h3{font-size:17px;font-weight:900;margin-bottom:8px}
  .vision-card p{font-size:11.5px;line-height:1.5}

  /* Checks */
  .slide-checks .heading{top:56px}
  .link-lines{position:absolute;left:0;top:0}
  .check-pill{position:absolute;width:320px;height:96px;border-radius:48px;color:var(--white);display:flex;align-items:center;gap:14px;padding:0 24px}
  .check-pill.blue{background:var(--blue)}
  .check-pill.gold{background:var(--gold)}
  .check-pill.mirror{flex-direction:row-reverse;text-align:right}
  .check-pill h3{font-size:14px;font-weight:900;margin-bottom:4px}
  .check-pill p{font-size:10.5px;line-height:1.45}
  .check-icon{flex:none;width:54px;height:54px;border-radius:50%;background:var(--white);display:flex;align-items:center;justify-content:center}
  .hub{position:absolute;left:430px;top:278px;width:140px;height:140px;border-radius:50%;background:var(--white);border:3px solid #dfe5f0;display:flex;align-items:center;justify-content:center}
  .hub .brand{font-size:20px;color:var(--blue);gap:7px}
  .hub .brand-mark{width:12px;height:12px;background:var(--blue)}

  /* White label */
  .label-frame{position:absolute;left:90px;top:60px;width:250px;height:330px;background:var(--yellow)}
  .label-photo{left:120px;top:110px;width:230px;height:340px;background:linear-gradient(165deg,#efe7da,#d6c2a2 55%,#a8876a)}
  .label-text{position:absolute;left:420px;top:140px;width:480px}
  .label-text .heading{font-size:32px;line-height:1.15;margin-bottom:18px}

  /* Thanks */
  .thanks-bg{position:absolute;inset:0;background:linear-gradient(180deg,#ffffff 0%,#f3f6fb 55%,#dde6f3 100%)}
  .slide-thanks .brand{position:absolute;left:0;right:0;top:70px;justify-content:center;color:var(--blue);font-size:40px}
  .slide-thanks .brand-mark{background:var(--blue);width:26px;height:26px}
  .thanks-title{top:160px;font-size:88px;color:var(--ink);font-weight:900}
  .contact-row{position:absolute;left:70px;right:70px;top:348px;display:flex;justify-content:space-between}
  .contact{display:flex;align-items:flex-start;gap:14px;width:260px}
  .contact-icon{flex:none;width:44px;height:44px;border-radius:50%;background:var(--blue);display:flex;align-items:center;justify-content:center}
  .contact h4{font-size:15px;font-weight:900;text-transform:uppercase;margin:4px 0 5px}
  .contact p{font-size:12px;line-height:1.5;color:var(--text)}
  .copyright{top:506px;font-size:10px;color:var(--text)}
</style>
</head>
<body>

<section class="slide slide-welcome">
  <div class="welcome-bg" role="img" aria-label="City skyline photo with a blue tint"></div>
  <div class="brand"><span class="brand-mark"></span>Caldrift</div>
  <h1 class="heading welcome-title">Welcome to<br>Caldrift</h1>
  <p class="welcome-tagline">Moving For The Next Generation</p>
</section>

<section class="slide slide-about">
  <svg class="side-bars" viewBox="0 0 1000 562" aria-hidden="true">
    <polygon points="0,0 250,70 250,492 0,562" fill="var(--blue)"/>
    <polygon points="1000,40 958,82 958,480 1000,522" fill="var(--blue)"/>
  </svg>
  <div class="about-frame"></div>
  <div class="photo about-photo" role="img" aria-label="Photo of two people unpacking moving boxes in a bright office"></div>
  <div class="about-text">
    <h2 class="heading">About Us</h2>
    <p class="body-copy">Caldrift is the most logical evolution in professional moving. Professional moving that includes reliable pricing, secure capacity guarantees and concierge service options.</p>
    <p class="body-copy">Caldrift was founded by lifelong moving professionals who have developed the answer to better moving services. Rooted in transparent rates, verified surveys and a dependable partner network, we offer a smarter alternative. We are a technology-first organization using proprietary software to deliver moving services.</p>
  </div>
</section>

<section class="slide slide-vision">
  <svg class="side-bars" viewBox="0 0 1000 562" aria-hidden="true">
    <polygon points="0,40 42,82 42,480 0,522" fill="var(--blue)"/>
    <polygon points="1000,40 958,82 958,480 1000,522" fill="var(--blue)"/>
  </svg>
  <h2 class="heading centered-title" style="top:56px">Caldrift Vision</h2>
  <p class="centered-title vision-sub">The traditional moving industry is broken, outdated, inefficient, and unable to change.</p>
  <article class="vision-card blue" style="left:210px">
    <div class="card-photo" role="img" aria-label="Photo of a mover carrying boxes" style="background:linear-gradient(160deg,#b9c6d6,#6f7f95)"></div>
    <h3>Our Vision</h3>
    <p>To become the most trusted name in modern, hassle-free moving.</p>
  </article>
  <article class="vision-card yellow" style="left:410px">
    <div class="card-photo" role="img" aria-label="Photo of a team joining hands" style="background:linear-gradient(160deg,#e6dccb,#a99279)"></div>
    <h3>Our Mission</h3>
    <p>Deliver honest pricing, secured capacity and reliable service on every move.</p>
  </article>
  <article class="vision-card blue" style="left:610px">
    <div class="card-photo" role="img" aria-label="Photo of a person celebrating a goal" style="background:linear-gradient(160deg,#4d6fae,#1c2f5e)"></div>
    <h3>Our Goal</h3>
    <p>Make every relocation simple, affordable and stress free for each customer.</p>
  </article>
</section>

<section class="slide slide-checks">
  <svg class="side-bars" viewBox="0 0 1000 562" aria-hidden="true">
    <polygon points="0,40 42,82 42,480 0,522" fill="var(--blue)"/>
    <polygon points="1000,40 958,82 958,480 1000,522" fill="var(--blue)"/>
    <line x1="450" y1="268" x2="550" y2="268" stroke="#dfe5f0" stroke-width="3"/>
    <line x1="450" y1="428" x2="550" y2="428" stroke="#dfe5f0" stroke-width="3"/>
    <line x1="500" y1="230" x2="500" y2="466" stroke="#dfe5f0" stroke-width="3"/>
  </svg>
  <h2 class="heading centered-title">Caldrift Built-In Checks and Balances</h2>

  <div class="check-pill blue" style="left:130px;top:220px">
    <div><h3>Independent Survey Company</h3><p>Every move is surveyed by a third party to confirm inventory and weight before pickup.</p></div>
  </div>
  <div class="check-pill gold mirror" style="left:550px;top:220px">
    <span class="check-icon"><svg width="28" height="28" viewBox="0 0 24 24"><path d="M5 12l5 5 9-10" fill="none" stroke="var(--gold)" stroke-width="2.6" stroke-linecap="round" stroke-linejoin="round"/></svg></span>
    <div><h3>Immediate Capacity Secured</h3><p>Truck space and crew are reserved the moment your booking is confirmed.</p></div>
  </div>
  <div class="check-pill gold" style="left:130px;top:380px">
    <div><h3>Multiple Vetted Service Providers</h3><p>A vetted network of carriers ensures backup options are always ready.</p></div>
  </div>
  <div class="check-pill blue mirror" style="left:550px;top:380px">
    <span class="check-icon"><svg width="28" height="28" viewBox="0 0 24 24"><circle cx="12" cy="9" r="5" fill="none" stroke="var(--blue)" stroke-width="2.4"/><path d="M8 14l-2 7 6-3 6 3-2-7" fill="none" stroke="var(--blue)" stroke-width="2.2" stroke-linejoin="round"/></svg></span>
    <div><h3>Concierge Service</h3><p>A dedicated coordinator guides you from first quote to final delivery.</p></div>
  </div>

  <div class="hub"><div class="brand"><span class="brand-mark"></span>Caldrift</div></div>
</section>

<section class="slide slide-label">
  <svg class="side-bars" viewBox="0 0 1000 562" aria-hidden="true">
    <polygon points="0,40 42,82 42,480 0,522" fill="var(--blue)"/>
    <polygon points="1000,40 958,82 958,480 1000,522" fill="var(--blue)"/>
  </svg>
  <div class="label-frame"></div>
  <div class="photo label-photo" role="img" aria-label="Photo of a room filled with stacked cardboard moving boxes"></div>
  <div class="label-text">
    <h2 class="heading">Caldrift White<br>Label</h2>
    <p class="body-copy">Caldrift offers a white labeling solution for companies looking to expand their reach and customer base. Our technology platform can be customized with your branding and integrates seamlessly with your existing systems and processes. This allows you to offer a top-notch moving experience to your customers while leveraging the strength of Caldrift's proven technology. With this solution you can streamline operations, increase customer satisfaction and capture more revenue in the growing world of digital moving.</p>
  </div>
</section>

<section class="slide slide-thanks">
  <div class="thanks-bg" role="img" aria-label="Faded city skyline photo"></div>
  <svg class="side-bars" viewBox="0 0 1000 562" aria-hidden="true">
    <polygon points="1000,40 958,82 958,480 1000,522" fill="var(--blue)"/>
  </svg>
  <div class="brand"><span class="brand-mark"></span>Caldrift</div>
  <h2 class="heading centered-title thanks-title">Thank You</h2>
  <div class="contact-row">
    <div class="contact">
      <span class="contact-icon"><svg width="20" height="20" viewBox="0 0 24 24"><path d="M12 2a7 7 0 0 0-7 7c0 5 7 13 7 13s7-8 7-13a7 7 0 0 0-7-7z" fill="var(--white)"/><circle cx="12" cy="9" r="2.6" fill="var(--blue)"/></svg></span>
      <div><h4>Address</h4><p>2140 Harbor Lane<br>Westfield, CO 80421</p></div>
    </div>
    <div class="contact">
      <span class="contact-icon"><svg width="20" height="20" viewBox="0 0 24 24"><path d="M6.6 10.8a15 15 0 0 0 6.6 6.6l2.2-2.2a1 1 0 0 1 1-.25 11.4 11.4 0 0 0 3.6.57 1 1 0 0 1 1 1V20a1 1 0 0 1-1 1A17 17 0 0 1 3 4a1 1 0 0 1 1-1h3.5a1 1 0 0 1 1 1 11.4 11.4 0 0 0 .57 3.6 1 1 0 0 1-.25 1z" fill="var(--white)"/></svg></span>
      <div><h4>Contact Number</h4><p>(555) 018-2746</p></div>
    </div>
    <div class="contact">
      <span class="contact-icon"><svg width="20" height="20" viewBox="0 0 24 24"><rect x="3" y="5" width="18" height="14" rx="2" fill="var(--white)"/><path d="M4 7l8 6 8-6" fill="none" stroke="var(--blue)" stroke-width="1.8"/></svg></span>
      <div><h4>Email Address</h4><p>hello@caldrift.com</p></div>
    </div>
  </div>
  <p class="centered-title copyright">© Copyright 2024 Caldrift. All Rights Reserved.</p>
</section>

</body>
</html>
```